Signage Design Project

Busisness is a bakery and deli long time owned by the Tavel family. Want to develop a new outside sign that communicates it is a deli and a bakery but keeps the tavel name in the design.

The sign when produced will be about 10' by 3' . It is not lighted at present but could be if it were advantageous.

The name of the store is:

Tavel's Harbor Lane Bakery and Deli. The concept is to have a new,modern sign that reinforces that it is a deli and a bakery, as most people only know about the bakery side of the business
Updates

The name Tavel is just a reinforcer so the people kno it is still in the family.  The emphasis should be on the HARBOR LANE BAKERY and DELI

Target Market(s)

Small business breakfast and lunch customers

Industry/Entity Type

Bakery

Requirements
Must have
• Great impact from the road. Communicate that it is a deli and a bakery. Keep the Tavel name but need not be a major design element

```html
<!DOCTYPE html>
<html lang="en">
<head>
<meta charset="utf-8">
<title>Tavel's Harbor Lane Bakery and Deli – Sign</title>
<link rel="stylesheet" href="https://fonts.googleapis.com/css2?family=Berkshire+Swash&family=Righteous&display=swap">
<style>
  :root {
    --sign-pink: #e6007e;
    --sign-shadow: #1a1a1a;
    --sign-yellow-core: #f8ea2f;
    --sign-yellow-mid: #faf07a;
    --sign-yellow-edge: #fdf6bd;
    --ornament-tone: #f7e87a;
  }
  html, body {
    margin: 0;
    padding: 0;
    overflow: hidden;
    background: #ffffff;
  }
  .sign {
    position: relative;
    width: 1200px;
    height: 360px;
    overflow: hidden;
    background: radial-gradient(ellipse 50% 75% at 50% 50%,
      var(--sign-yellow-core) 0%,
      var(--sign-yellow-mid) 65%,
      var(--sign-yellow-edge) 100%);
  }
  .sign__ornament {
    position: absolute;
    top: 14px;
    width: 68px;
    height: 332px;
    border-radius: 30px;
    background: linear-gradient(180deg, var(--sign-yellow-edge), var(--ornament-tone) 50%, var(--sign-yellow-edge));
  }
  .sign__ornament--left { left: 16px; }
  .sign__ornament--right { right: 16px; }
  .sign__family-line {
    position: absolute;
    left: 0;
    right: 0;
    top: 18px;
    text-align: center;
    font-family: "Berkshire Swash", cursive;
    color: var(--sign-pink);
    text-shadow: 3px 3px 0 var(--sign-shadow);
    white-space: nowrap;
    line-height: 1;
  }
  .sign__family-name {
    font-size: 54px;
    margin-right: 8px;
  }
  .sign__place-name {
    font-size: 100px;
  }
  .sign__trade-line {
    position: absolute;
    left: 0;
    right: 0;
    top: 170px;
    margin: 0;
    text-align: center;
    font-family: "Righteous", sans-serif;
    font-weight: 400;
    font-size: 128px;
    line-height: 1;
    color: var(--sign-pink);
    text-shadow: 4px 4px 0 var(--sign-shadow);
    letter-spacing: 2px;
    white-space: nowrap;
  }
</style>
</head>
<body>
  <div class="sign">
    <div class="sign__ornament sign__ornament--left" role="img" aria-label="Decorative yellow scroll flourish along the left edge"></div>
    <div class="sign__ornament sign__ornament--right" role="img" aria-label="Decorative yellow scroll flourish along the right edge"></div>
    <div class="sign__family-line">
      <span class="sign__family-name">Tavel's</span><span class="sign__place-name">Harbor Lane</span>
    </div>
    <h1 class="sign__trade-line">Bakery and Deli</h1>
  </div>
</body>
</html>
```